e-commerce store for sport clothing online store "baseball merchandise "web application...

I want to design a UX/UI for my web application website for the online store I will provide you with the following:
1. screen shots of the initial design for the pages>
2. the logo files.
3. The brand guideline file.

the provided files (screen shots) is guideline I want to see CREATIVITY with the UX/UI DESIGN.
PS. PLEASE FOLLOW THE BRANDGUIDE LINE CAREFULLY SPECIALLY THE TYPOGRAPHY & THE COLOR CODES.

PLEASE VISIT THIS WEBSITE brightlane.varomi-qz.com to see more for the screens.

```html
<!DOCTYPE html>
<html lang="en">
<head>
<meta charset="UTF-8">
<title>Checkout – Payment Details</title>
<link href="https://fonts.googleapis.com/css2?family=Lato:wght@400;700;900&display=swap" rel="stylesheet">
<style>
  :root {
    --navy: #10213f;
    --white: #ffffff;
    --card: #d9d9d9;
    --ink: #111111;
    --black: #000000;
    --line: #10213f;
  }
  * { box-sizing: border-box; margin: 0; padding: 0; }
  html, body { width: 1200px; height: 2667px; overflow: hidden; background: var(--white); }
  body { font-family: "Lato", Arial, sans-serif; color: var(--ink); position: relative; }

  .app-header {
    position: absolute; left: 0; top: 0; width: 1200px; height: 267px;
    background: var(--navy); color: var(--white);
  }
  .back-button { position: absolute; left: 75px; top: 103px; width: 64px; height: 64px; }
  .header-title {
    position: absolute; left: 0; right: 0; top: 100px; text-align: center;
    font-size: 52px; font-weight: 900; line-height: 66px;
  }

  .stepper { position: absolute; left: 0; top: 390px; width: 1200px; height: 270px; }
  .stepper-line { position: absolute; top: 66px; height: 4px; background: var(--line); }
  .step { position: absolute; width: 260px; margin-left: -130px; text-align: center; }
  .step-circle {
    width: 132px; height: 132px; margin: 0 auto; border-radius: 50%;
    border: 4px solid var(--navy); display: flex; align-items: center; justify-content: center;
    font-size: 58px; font-weight: 900; background: var(--white); color: var(--navy);
  }
  .step.is-done .step-circle { background: var(--navy); color: var(--white); }
  .step-label { margin-top: 14px; font-size: 40px; line-height: 50px; color: var(--ink); }

  .section-title {
    position: absolute; left: 47px; top: 735px;
    font-size: 52px; font-weight: 700; line-height: 66px;
  }

  .payment-option {
    position: absolute; left: 47px; width: 1093px; height: 193px;
    background: var(--card); border-radius: 13px;
  }
  .payment-option .selector { position: absolute; left: 113px; top: 67px; width: 60px; height: 60px; }
  .payment-option .option-name {
    position: absolute; left: 177px; top: 66px; font-size: 50px; line-height: 62px;
  }
  .payment-option .provider-mark {
    position: absolute; right: 40px; top: 74px; display: flex; align-items: center; gap: 14px;
    font-size: 34px; font-weight: 700; color: var(--navy); line-height: 44px;
  }
  .provider-mark .mark-square { width: 34px; height: 34px; background: var(--navy); border-radius: 4px; }

  .action-bar {
    position: absolute; left: 0; top: 2473px; width: 1200px; height: 194px;
    background: var(--white); border-radius: 40px 40px 0 0;
    box-shadow: 0 -4px 18px rgba(0,0,0,0.18);
  }
  .proceed-button {
    position: absolute; left: 40px; top: 24px; width: 1120px; height: 143px;
    background: var(--black); color: var(--white); border: none; border-radius: 13px;
    font-family: "Lato", Arial, sans-serif; font-size: 47px; font-weight: 900;
  }
</style>
</head>
<body>
  <header class="app-header">
    <svg class="back-button" viewBox="0 0 24 24" aria-label="Back">
      <path d="M20 12H5M11 5l-7 7 7 7" fill="none" stroke="#ffffff" stroke-width="2.4" stroke-linecap="round" stroke-linejoin="round"/>
    </svg>
    <h1 class="header-title">Checkout</h1>
  </header>

  <nav class="stepper" aria-label="Checkout progress">
    <div class="stepper-line" style="left:330px;width:210px"></div>
    <div class="stepper-line" style="left:664px;width:210px"></div>
    <div class="step is-done" style="left:267px">
      <div class="step-circle">1</div>
      <div class="step-label">Shipping<br>Details</div>
    </div>
    <div class="step is-done" style="left:600px">
      <div class="step-circle">2</div>
      <div class="step-label">Payment<br>Details</div>
    </div>
    <div class="step" style="left:937px">
      <div class="step-circle">3</div>
      <div class="step-label">Confirmation</div>
    </div>
  </nav>

  <h2 class="section-title">Payment Method</h2>

  <div class="payment-option is-selected" style="top:850px">
    <svg class="selector" viewBox="0 0 20 20" aria-label="Selected">
      <circle cx="10" cy="10" r="10" fill="#10213f"/>
      <path d="M5.5 10.2l3 3 6-6" fill="none" stroke="#ffffff" stroke-width="2" stroke-linecap="round" stroke-linejoin="round"/>
    </svg>
    <span class="option-name">Nexapay</span>
    <span class="provider-mark"><span class="mark-square"></span>Nexapay</span>
  </div>

  <div class="payment-option" style="top:1100px">
    <svg class="selector" viewBox="0 0 20 20" aria-label="Not selected">
      <circle cx="10" cy="10" r="8.8" fill="none" stroke="#10213f" stroke-width="1.8"/>
    </svg>
    <span class="option-name">Cardline</span>
    <span class="provider-mark">Cardline</span>
  </div>

  <footer class="action-bar">
    <button class="proceed-button">Proceed</button>
  </footer>
</body>
</html>
```